Business Cards - New Logo Rebranding

Hello We know have a red and blue logo and are looking to create new cards. We are looking for the best creativity of the new logo merged with some of the existing artwork provided.

Target Market(s)

Realtors

Industry/Entity Type

Real Estate

Contact Information for Business Card

New logo with rebranded colors

Requirements
Must have
• Creative use of the new logo

```html
<!DOCTYPE html>
<html lang="en">
<head>
<meta charset="utf-8">
<title>Summit Crest – Business Card</title>
<link rel="stylesheet" href="https://fonts.googleapis.com/css2?family=PT+Sans:wght@400;700&family=Poppins:wght@700&family=Roboto+Condensed:wght@700&display=swap">
<style>
  :root {
    --bg: #a6a6a6;
    --white: #ffffff;
    --blue: #0b6fc2;
    --blue-name: #1565c0;
    --red: #e0353d;
    --ink: #333333;
    --photo-a: #0a6fd0;
    --photo-b: #1d8fe8;
    --badge-gold: #c9a93a;
    --badge-silver: #b9b9b0;
    --badge-navy: #23336f;
    --badge-red: #c8202b;
  }
  * { box-sizing: border-box; margin: 0; padding: 0; }
  html, body { width: 1093px; height: 1200px; overflow: hidden; }
  body { background: var(--bg); position: relative; font-family: "PT Sans", sans-serif; }

  .card { position: absolute; left: 265px; width: 578px; height: 357px; border-radius: 22px; overflow: hidden; }
  .card--front { top: 226px; background: var(--white); }
  .card--back { top: 621px; background: var(--blue); }

  /* Front */
  .brand { position: absolute; left: 28px; top: 30px; width: 204px; text-align: center; }
  .brand__mark { display: block; margin: 0 auto 10px; width: 100px; height: 100px; border-radius: 50%; background: var(--blue); border: 4px solid var(--red); }
  .brand__name { font-family: "Poppins", sans-serif; font-weight: 700; font-size: 22px; color: var(--blue); letter-spacing: 1px; }

  .contact { position: absolute; left: 26px; top: 203px; list-style: none; }
  .contact li { display: flex; align-items: center; height: 20.3px; font-size: 16px; color: var(--ink); }
  .contact svg { width: 14px; height: 14px; margin-right: 5px; fill: var(--red); flex: none; }

  .portrait { position: absolute; left: 383px; top: 35px; width: 162px; height: 197px; border-radius: 9px; background: radial-gradient(circle at 55% 35%, var(--photo-b), var(--photo-a) 75%); }

  .person { position: absolute; right: 32px; top: 236px; text-align: right; }
  .person__name { font-weight: 700; font-size: 23px; line-height: 1.1; }
  .person__first { color: var(--blue-name); }
  .person__last { color: var(--red); }
  .person__title { font-size: 16px; color: var(--ink); }

  .services { position: absolute; left: 0; right: 0; bottom: 0; height: 44px; background: var(--blue); color: var(--white); font-size: 17px; display: flex; align-items: center; justify-content: center; word-spacing: 1px; }

  /* Back */
  .headline { position: absolute; left: 0; right: 0; top: 0; height: 71px; background: var(--red); color: var(--white); font-family: "Poppins", sans-serif; font-weight: 700; font-size: 20.5px; line-height: 27px; text-align: center; padding-top: 8px; }
  .why { position: absolute; left: 33px; top: 83px; color: var(--white); font-family: "Poppins", sans-serif; font-weight: 700; font-size: 18px; }
  .reasons { position: absolute; left: 31px; top: 119px; list-style: none; }
  .reasons li { display: flex; align-items: center; height: 33.5px; color: var(--white); font-family: "Roboto Condensed", sans-serif; font-weight: 700; font-size: 14.5px; }
  .reasons li::before { content: ""; width: 14px; height: 14px; border-radius: 50%; border: 2px solid var(--white); margin-right: 5px; flex: none; }

  .badge { position: absolute; }
  .badge--round { width: 46px; height: 46px; border-radius: 50%; top: 239px; }
  .badge--heroes { left: 370px; background: var(--badge-navy); border: 4px solid var(--badge-red); }
  .badge--master { left: 436px; background: var(--badge-gold); }
  .badge--cpi { left: 502px; background: var(--badge-silver); }
  .badge--drone { left: 363px; top: 293px; width: 80px; height: 37px; background: var(--badge-navy); border: 2px solid var(--badge-gold); border-radius: 4px; }
  .badge--reviews { left: 457px; top: 290px; width: 56px; height: 36px; background: var(--white); border-radius: 4px; }
  .badge--infrared { left: 531px; top: 290px; width: 30px; height: 36px; background: var(--white); border-radius: 4px; }
</style>
</head>
<body>

<section class="card card--front">
  <div class="brand">
    <span class="brand__mark"></span>
    <div class="brand__name">SUMMIT CREST</div>
  </div>

  <ul class="contact">
    <li><svg viewBox="0 0 16 16"><path d="M2 6c0-2 3-3 6-3s6 1 6 3v1h-3V6H5v1H2zM4 8h8l2 6H2z"/></svg>800.555.0142</li>
    <li><svg viewBox="0 0 16 16"><path d="M4 1h8v14H4zM5.5 2.5v9h5v-9zM7 12.5h2v1.5H7z"/></svg>555.204.7731</li>
    <li><svg viewBox="0 0 16 16"><path d="M1 3h14v10H1zM2.5 4.5 8 9l5.5-4.5v-.2H2.5z"/></svg>danielmoreno@summitcrestinspect.com</li>
    <li><svg viewBox="0 0 16 16"><circle cx="8" cy="8" r="7"/></svg>www.SummitCrestInspect.com</li>
  </ul>

  <div class="portrait" role="img" aria-label="Portrait photo of the inspector in a blue company polo against a blue backdrop"></div>

  <div class="person">
    <div class="person__name"><span class="person__first">Daniel</span> <span class="person__last">Moreno</span></div>
    <div class="person__title">Certified Mold Inspector</div>
  </div>

  <div class="services">HOME | SEWER | MOLD | COMMERCIAL | TERMITE | ROOF</div>
</section>

<section class="card card--back">
  <div class="headline">CALIFORNIA'S #1<br>INSPECTION COMPANY!</div>
  <div class="why">WHY CHOOSE SUMMIT CREST...</div>
  <ul class="reasons">
    <li>Performing Inspections Since 1984</li>
    <li>NationCert Certified Master / Professional Inspectors®</li>
    <li>500,000+ Inspections Completed Statewide</li>
    <li>Request of Repairs Pricer Report</li>
    <li>90-Day Inspection Guarantees</li>
    <li>AVFA Drone Licensed Roof Inspectors upon request</li>
    <li>5,000+ 5-Star Reviews on Searchly &amp; Rateo</li>
  </ul>

  <span class="badge badge--round badge--heroes" role="img" aria-label="Heroes discount program badge"></span>
  <span class="badge badge--round badge--master" role="img" aria-label="Certified master inspector seal"></span>
  <span class="badge badge--round badge--cpi" role="img" aria-label="Certified professional inspector seal"></span>
  <span class="badge badge--drone" role="img" aria-label="Certified drone pilot badge"></span>
  <span class="badge badge--reviews" role="img" aria-label="Five-star review listing badge"></span>
  <span class="badge badge--infrared" role="img" aria-label="Infrared certified badge"></span>
</section>

</body>
</html>
```